Web page for a garment manufacturing company

We are clothing manufacturer based in Romania.
With our recent expansion, we have significantly increased our internal capacity, allowing us to take on new partnerships and deliver high-quality production services.
Our expertise includes producing classic coats, blazers, trousers, skirts, dresses, and blouses, though we are flexible and open to working with various other textile products.

Target Market(s)

High-end market and luxury

Industry/Entity Type

Garments Manufacturer

Coding

Coded - Design and coding required

Number of Pages Required

1 page

Colors

Designer to choose only greyscale colors for use in the design.

Requirements
Must have
• Velmora logo from our presentation
Nice to have
• https://www.lorvani.pt/
Should not have
• prices, wedding dresses, collections

```html
<!DOCTYPE html>
<html lang="en">
<head>
<meta charset="utf-8">
<title>Velmora – Clothing Manufacturer</title>
<link href="https://fonts.googleapis.com/css2?family=Lexend:wght@400;500;600;700&family=Noto+Sans:wght@400;500;600&display=swap" rel="stylesheet">
<style>
:root{
  --ink:#262626;
  --ink-dark:#2b2b2b;
  --accent:#555555;
  --accent-soft:#c4c4c4;
  --page:#eeeeee;
  --white:#ffffff;
  --muted:#666666;
  --line:#c9c9c9;
  --dot:#c6c6c6;
  --badge-1:#6e6e6e;
  --badge-2:#d2d2d2;
  --badge-3:#4a4a4a;
  --badge-4:#3a3a3a;
  --badge-5:#8a8a8a;
}
*{margin:0;padding:0;box-sizing:border-box}
html,body{width:1200px;height:4255px;overflow:hidden}
body{background:var(--page);font-family:"Noto Sans",sans-serif;color:var(--ink);position:relative}
.abs{position:absolute}
.head{font-family:"Lexend",sans-serif}
/* hero */
.hero{left:0;top:0;width:1200px;height:625px;background:linear-gradient(180deg,#5a5a5a 0%,#424242 45%,#6a6a6a 100%)}
.hero-title{top:300px;width:1200px;text-align:center;color:#fff;font-size:46px;font-weight:600}
.hero-sub{top:375px;width:1200px;text-align:center;color:#fff;font-size:23px;line-height:29px}
.nav{left:33px;top:33px;width:1134px;height:83px;background:var(--white);border-radius:16px}
.logo{font-family:"Lexend",sans-serif;font-weight:400;font-size:32px;color:#444}
.nav .logo{left:33px;top:20px}
.nav-links{left:228px;top:28px;display:flex;gap:34px;font-size:21px;color:var(--ink)}
.nav-links span::after{content:"";display:inline-block;width:8px;height:8px;border-right:2px solid var(--ink);border-bottom:2px solid var(--ink);transform:rotate(45deg);margin:0 0 5px 10px}
.contact-btn{left:942px;top:20px;width:192px;height:42px;background:var(--ink);border-radius:6px;color:#fff;font-size:16px;font-weight:600;display:flex;align-items:center;justify-content:center;gap:8px}
/* about */
.label{font-family:"Lexend",sans-serif;font-size:29px;font-weight:500}
.about-title{left:66px;top:728px;font-size:48px;line-height:56px;font-weight:600}
.btn{background:var(--accent);color:#fff;font-family:"Lexend",sans-serif;font-size:20px;display:flex;align-items:center;justify-content:center}
.about-photo{left:66px;top:997px;width:367px;height:405px;background:linear-gradient(160deg,#cfcfcf,#8e8e8e 60%,#a6a6a6);clip-path:polygon(0 0,100% 0,100% 85%,85% 100%,0 100%)}
.about-frame{left:74px;top:1005px;width:367px;height:405px;background:var(--accent-soft);clip-path:polygon(0 0,100% 0,100% 85%,85% 100%,0 100%)}
.about-text{left:562px;top:730px;width:572px;font-size:20px;line-height:26.6px;color:#222}
.about-text p+p{margin-top:20px}
.stat{top:1152px;text-align:center}
.stat b{display:block;font-family:"Lexend",sans-serif;font-size:36px;font-weight:500}
.stat span{font-size:16px;font-weight:500}
/* cert */
.cert{left:66px;top:1461px;width:1066px;height:215px;border:3px solid var(--line)}
.cert h2{text-align:center;margin-top:20px;font-size:45px;font-weight:600}
/* benefits */
.center{width:1200px;text-align:center}
.sec-title{font-size:47px;font-weight:600}
.sec-sub{font-size:30px;font-weight:500}
.benefits{left:66px;top:1860px;width:1066px;height:479px;background:var(--white)}
.benefit{width:250px}
.benefit svg{display:block;margin-bottom:14px}
.benefit h3{font-family:"Lexend",sans-serif;font-size:18px;font-weight:600;line-height:23px}
.benefit p{font-size:14.5px;line-height:21.5px;color:var(--muted);margin-top:8px}
/* work */
.card-img{border-radius:12px;box-shadow:0 4px 12px rgba(0,0,0,.2)}
.dot{width:13px;height:13px;border-radius:50%;background:var(--dot);top:3128px}
/* activity */
.act-img{top:3341px;width:340px;height:211px;border-radius:10px}
.act h3{font-family:"Lexend",sans-serif;font-size:23px;font-weight:600}
.act p{font-size:18px;line-height:27px;color:var(--muted);margin-top:10px}
.act hr{border:0;border-top:2px solid var(--ink);width:168px;margin:18px 0 12px}
.act time{font-family:"Lexend",sans-serif;font-size:17px;font-weight:500}
/* footer */
.footer{left:0;top:3896px;width:1200px;height:359px;background:var(--ink-dark);color:#fff}
.footer .logo{color:#fff;left:66px;top:60px;font-size:34px}
.foot-links{right:66px;top:70px;display:flex;gap:46px;font-family:"Lexend",sans-serif;font-size:20px}
.foot-rule{left:66px;top:128px;width:1068px;height:2px;background:#fff}
.foot-addr{left:66px;top:164px;font-size:18px;line-height:25px}
.social{width:38px;height:38px;border-radius:50%;background:#fff;top:165px}
.foot-contact{right:66px;top:221px;text-align:right;font-size:18px;line-height:25px}
.copy{top:306px;font-size:17px}
</style>
</head>
<body>

<header>
  <div class="abs hero" role="img" aria-label="Aerial view of the factory campus with solar roofs"></div>
  <h1 class="abs hero-title head">When Fashion meets Quality!</h1>
  <p class="abs hero-sub">Committed to shape the future of the textile industry and<br>together becoming the Clothing Manufacturer of the Future!</p>
  <nav class="abs nav">
    <div class="abs logo">Velmora</div>
    <div class="abs nav-links"><span>Home</span><span>Our Work</span><span>Concept</span><span>News</span><span>Get In Touch</span></div>
    <div class="abs contact-btn">
      <svg width="18" height="18" viewBox="0 0 24 24"><path fill="#fff" d="M6.6 10.8a15 15 0 006.6 6.6l2.2-2.2a1 1 0 011-.25 11.4 11.4 0 003.6.6 1 1 0 011 1V20a1 1 0 01-1 1A17 17 0 013 4a1 1 0 011-1h3.5a1 1 0 011 1c0 1.25.2 2.45.6 3.6a1 1 0 01-.25 1z"/></svg>
      Contact Us
    </div>
  </nav>
</header>

<section class="about">
  <div class="abs label" style="left:66px;top:682px">About</div>
  <h2 class="abs about-title head">The Top<br>Manufacture<br>Company</h2>
  <div class="abs btn" style="left:66px;top:921px;width:207px;height:36px">Read More</div>
  <div class="abs about-frame"></div>
  <div class="abs about-photo" role="img" aria-label="Factory floor with rows of garments on hanging rails"></div>
  <div class="abs about-text">
    <p><b>VELMORA</b> is a manufacturing company for Ready-to-wear, situated in Varnesti, a city with a rich tradition in the clothing industry. The top management is international, and we are proud to have a diverse and dynamic group of professionals from different countries working together. With our optimistic team spirit and passion for high-quality production to meet our customers' expectations, we are ready to take on new challenges &amp; delight our clients with excellent results.</p>
    <p>Established in 2005, we have produced a variety of different specialty workshops namely woven garments, knitwear, leather goods, bags, leather accessories, bed linen and are always open to new project &amp; challenges.</p>
  </div>
  <div class="abs stat" style="left:562px"><b>19+</b><span>Year of Experience</span></div>
  <div class="abs stat" style="left:766px"><b>15+</b><span>Award Winning</span></div>
  <div class="abs stat" style="left:941px"><b>100k</b><span>Production/month</span></div>
  <div class="abs" style="left:562px;top:1252px;width:300px;height:2px;background:var(--ink)"></div>
</section>

<section class="abs cert">
  <h2 class="head">Certificate</h2>
  <svg class="abs" style="left:0;top:105px" width="1066" height="90" viewBox="0 0 1066 90">
    <circle cx="161" cy="45" r="37" fill="var(--badge-1)"/>
    <circle cx="276" cy="45" r="37" fill="var(--badge-2)"/>
    <circle cx="395" cy="45" r="37" fill="var(--badge-3)"/>
    <rect x="472" y="20" width="250" height="52" rx="6" fill="var(--badge-4)"/>
    <rect x="768" y="16" width="160" height="60" rx="30" fill="var(--badge-5)"/>
  </svg>
</section>

<section class="benefits-sec">
  <h2 class="abs center head sec-title" style="top:1732px">Our Main Benefits</h2>
  <p class="abs center head sec-sub" style="top:1797px">We offer quality, with the best materials and service</p>
  <div class="abs benefits">
    <div class="abs benefit" style="left:109px;top:40px">
      <svg width="42" height="36" viewBox="0 0 42 36"><path d="M4 28a17 17 0 0134 0z" fill="#111"/><rect x="0" y="28" width="42" height="7" rx="2" fill="#111"/></svg>
      <h3>Prioritize worker<br>well-being</h3>
      <p>We support the physical and mental well-being of our workers.</p>
    </div>
    <div class="abs benefit" style="left:408px;top:40px">
      <svg width="42" height="40" viewBox="0 0 42 40"><circle cx="21" cy="15" r="13" fill="none" stroke="#111" stroke-width="4"/><path d="M12 26l-4 13 7-3 4 4 2-12zM30 26l4 13-7-3-4 4-2-12z" fill="#111"/></svg>
      <h3>High-quality products<br>and services</h3>
      <p>Focusing on quality, durability, and customer satisfaction.</p>
    </div>
    <div class="abs benefit" style="left:709px;top:40px">
      <svg width="42" height="40" viewBox="0 0 42 40"><path d="M21 2L2 18v20h38V18z" fill="none" stroke="#111" stroke-width="4"/><path d="M12 32c0-9 8-14 18-14-2 10-8 14-18 14z" fill="#111"/></svg>
      <h3>Environmental<br>responsibility</h3>
      <p>Minimizing our environmental impact by adopting sustainable practices</p>
    </div>
    <div class="abs benefit" style="left:260px;top:245px">
      <svg width="42" height="36" viewBox="0 0 42 36"><circle cx="15" cy="9" r="8" fill="#111"/><circle cx="29" cy="10" r="7" fill="#111"/><path d="M0 36c0-12 7-17 15-17s15 5 15 17zM26 20c9 0 16 5 16 16h-10c0-7-2-12-6-16z" fill="#111"/></svg>
      <h3>Social<br>Responsibility</h3>
      <p>Actively contribute to the well-being of the communities in which we operate, supporting local causes and organizations.</p>
    </div>
    <div class="abs benefit" style="left:559px;top:245px">
      <svg width="40" height="40" viewBox="0 0 40 40"><path d="M16 4a13 13 0 00-7 24v6h14v-6a13 13 0 00-7-24z" fill="#111"/><rect x="10" y="36" width="12" height="4" fill="#111"/><path d="M32 2l2 5 5 2-5 2-2 5-2-5-5-2 5-2z" fill="#111"/></svg>
      <h3>Innovation and<br>Technology</h3>
      <p>Embrace innovation and leverage technology for production efficiency &amp; develop sustainable solutions</p>
    </div>
  </div>
</section>

<section class="work">
  <div class="abs label" style="left:66px;top:2399px">Our Work</div>
  <h2 class="abs head sec-title" style="left:66px;top:2448px">Structure of Our Clothing Manufacturer</h2>
  <div class="abs card-img" style="left:-20px;top:2618px;width:84px;height:423px;background:linear-gradient(180deg,#c2c2c2,#858585)" role="img" aria-label="Workshop interior"></div>
  <div class="abs card-img" style="left:78px;top:2618px;width:339px;height:423px;background:linear-gradient(180deg,#dcdcdc,#9e9e9e 70%,#313131)" role="img" aria-label="3D garment design software on a workstation"></div>
  <div class="abs card-img" style="left:430px;top:2547px;width:340px;height:423px;background:linear-gradient(180deg,#dddddd 0%,#6a6a6a 40%,#555555 75%,#969696 100%)" role="img" aria-label="Brick warehouse building with loading door"></div>
  <div class="abs card-img" style="left:782px;top:2618px;width:340px;height:423px;background:linear-gradient(180deg,#e5e5e5,#bababa 60%,#3f3f3f)" role="img" aria-label="Fabric testing machine in a lab"></div>
  <div class="abs card-img" style="left:1135px;top:2618px;width:90px;height:423px;background:linear-gradient(180deg,#cbcbcb,#959595)" role="img" aria-label="Production line"></div>
  <div class="abs center head" style="top:3000px;font-size:29px;font-weight:500">Warehouse</div>
  <div class="abs btn" style="left:443px;top:3046px;width:312px;height:38px">Read More</div>
  <div class="abs dot" style="left:532px"></div>
  <div class="abs dot" style="left:557px"></div>
  <div class="abs dot" style="left:583px;width:36px;border-radius:7px;background:var(--accent)"></div>
  <div class="abs dot" style="left:627px"></div>
  <div class="abs dot" style="left:653px"></div>
</section>

<section class="activity">
  <h2 class="abs center head sec-title" style="top:3197px">Velmora Activity</h2>
  <p class="abs center head sec-sub" style="top:3263px">Take a peek at our other activities</p>
  <div class="abs act-img" style="left:78px;background:linear-gradient(160deg,#555555,#8c8c8c 55%,#9c9c9c)" role="img" aria-label="Team group in matching shirts at summer camp"></div>
  <div class="abs act-img" style="left:430px;background:linear-gradient(180deg,#8e8e8e,#8a8a8a 55%,#6b6b6b)" role="img" aria-label="Carved pumpkins on shelves"></div>
  <div class="abs act-img" style="left:782px;background:linear-gradient(135deg,#d2d2d2,#8c8c8c 50%,#8a8a8a)" role="img" aria-label="Christmas themed drawings on a table"></div>
  <div class="abs act" style="left:78px;top:3578px;width:340px">
    <h3>Vacation at Summer Camp</h3>
    <p>Velmora takes a summer vacation together by going camping.</p>
    <hr><time>02 July 2023</time>
  </div>
  <div class="abs act" style="left:426px;top:3578px;width:350px">
    <h3>Velmora Halloween Party</h3>
    <p>Velmora selebrated the traditional Halloween Party with a lot of pumpkin.</p>
    <hr><time>28 October 2023</time>
  </div>
  <div class="abs act" style="left:782px;top:3578px;width:350px">
    <h3>Velmora Christmas Party</h3>
    <p>Velmora selebrated the Christmas Party with by drawing a Christmas theme for each other</p>
    <hr><time>25 December 2023</time>
  </div>
  <div class="abs btn" style="left:430px;top:3799px;width:339px;height:38px">All the News</div>
</section>

<footer class="abs footer">
  <div class="abs logo">Velmora</div>
  <div class="abs foot-links"><span>Home</span><span>Our Work</span><span>Concept</span><span>News</span><span>Get in Touch</span></div>
  <div class="abs foot-rule"></div>
  <div class="abs foot-addr"><b>Velmora Fashion</b><br>Str. Teilor 48<br>Varnesti, Romania<br>Zip Code: 627410</div>
  <div class="abs social" style="left:994px"></div>
  <div class="abs social" style="left:1044px"></div>
  <div class="abs social" style="left:1094px"></div>
  <div class="abs foot-contact">+40 300 555 018<br>hello@velmorafashion.com</div>
  <div class="abs center copy">Velmora © 2024 All Rights Reserved</div>
</footer>

</body>
</html>
```